Holistic/ Sports Psychologist needs flyer design

I need a flyer designed that catches the attention of potential customers - (parents of young athletes and athletes) who may be looking for psychological services. I have a logo and all the relevant info for the flyer but would like someone to take it and make it look creative, fun, fresh and attention getting for high school and college athletes. The colors used can be from my logo design which represents my holistic approach.
Target Market(s)
high school and collegiate athletes
Industry/Entity Type
sports psychology
Requirements
Must have
- Info I put on the flyer with my logo and please add some graphics and color based on my logo

```html
<!DOCTYPE html>
<html lang="en">
<head>
<meta charset="UTF-8">
<title>Holistic &amp; Sports Psychology Consulting – Flyer</title>
<link href="https://fonts.googleapis.com/css2?family=Poppins:wght@300;400;500;600;700&family=Handlee&display=swap" rel="stylesheet">
<style>
  :root {
    --navy: #27236b;
    --navy-deep: #221d5e;
    --blue: #3a73b8;
    --green: #9bce5a;
    --green-bright: #a5d65f;
    --white: #ffffff;
    --text: #3b3b55;
    --backdrop: #6f6f73;
  }
  * { margin: 0; padding: 0; box-sizing: border-box; }
  html, body { width: 869px; height: 1200px; overflow: hidden; background: var(--backdrop); }
  .canvas { position: relative; width: 869px; height: 1200px; overflow: hidden; background: var(--backdrop); font-family: "Poppins", sans-serif; }

  .page {
    position: absolute; top: 305px;
    width: 752px; height: 1068px;
    transform: scale(0.552); transform-origin: 0 0;
    overflow: hidden; background: var(--white); color: var(--text);
    box-shadow: 0 6px 18px rgba(0,0,0,0.35);
  }
  .page--front { left: 14px; }
  .page--back { left: 440px; }
  .layer { position: absolute; left: 0; top: 0; }

  /* Front */
  .brand-mark { position: absolute; left: 158px; top: 38px; width: 102px; height: 102px; border-radius: 50%; background: var(--white); border: 4px solid var(--blue); }
  .brand-bar { position: absolute; left: 260px; top: 98px; width: 335px; height: 22px; background: var(--green); }
  .brand-name { position: absolute; left: 276px; top: 62px; font-weight: 500; font-size: 27px; line-height: 34px; color: var(--blue); white-space: nowrap; }

  .hero-title {
    position: absolute; left: 0; top: 231px; width: 550px; height: 210px;
    background: rgba(39, 35, 107, 0.88);
    padding: 22px 0 0 40px;
    font-weight: 700; font-size: 44px; line-height: 55px; color: var(--white);
  }
  .hero-title .accent { color: var(--green-bright); }

  .section-head { position: absolute; left: 35px; top: 602px; }
  .section-head .kicker { font-weight: 500; font-size: 23px; line-height: 32px; color: var(--blue); }
  .section-head .headline { font-weight: 700; font-size: 30px; line-height: 36px; color: var(--green); }
  .section-head .sub { font-weight: 500; font-size: 23px; line-height: 32px; color: var(--navy); }
  .section-rule { position: absolute; left: 33px; top: 715px; width: 452px; height: 6px; background: var(--green); }

  .services { position: absolute; left: 33px; top: 752px; width: 690px; list-style: none; }
  .services li { position: relative; padding-left: 28px; font-size: 14px; line-height: 18px; color: var(--text); }
  .services li + li { margin-top: 13px; }
  .services .tick { position: absolute; left: 0; top: 2px; width: 16px; height: 16px; }
  .services .label { font-weight: 500; font-size: 17px; color: var(--navy); }

  /* Back */
  .about-tab {
    position: absolute; left: 0; top: 42px; width: 355px; height: 50px;
    background: var(--blue); border-radius: 0 25px 25px 0;
    padding-left: 35px;
    font-weight: 300; font-size: 38px; line-height: 50px; color: var(--white); letter-spacing: 0.5px;
  }
  .about-text { position: absolute; left: 33px; top: 114px; width: 690px; font-size: 16.5px; line-height: 21px; color: var(--text); }
  .about-text + .about-text { top: 244px; }
  .about-text strong { font-weight: 600; color: var(--navy); }
  .about-text .lead { font-weight: 600; color: var(--blue); }

  .telehealth {
    position: absolute; left: 440px; top: 400px; width: 300px; text-align: center;
    font-family: "Handlee", cursive; font-size: 33px; line-height: 42px; color: var(--white);
  }
  .telehealth .accent { color: var(--green-bright); }
  .sessions { position: absolute; left: 460px; top: 556px; width: 262px; text-align: center; font-size: 22px; line-height: 30px; color: var(--white); }
  .sessions-pill {
    position: absolute; left: 460px; top: 591px; width: 262px; height: 40px;
    background: var(--green); border-radius: 20px; text-align: center;
    font-family: "Handlee", cursive; font-size: 32px; line-height: 42px; color: var(--navy-deep);
  }

  .contact-tab {
    position: absolute; left: 77px; top: 822px; width: 188px; height: 32px;
    background: var(--navy); border-radius: 16px; text-align: center;
    font-size: 18px; line-height: 32px; color: var(--white);
  }
  .contact-list { position: absolute; left: 0; top: 866px; width: 413px; list-style: none; }
  .contact-list li { position: relative; padding-left: 119px; font-size: 18.5px; line-height: 31px; color: var(--white); }
  .contact-list li + li { border-top: 1px solid rgba(255,255,255,0.55); padding-top: 4px; padding-bottom: 4px; }
  .contact-list li:first-child { padding-bottom: 8px; }
  .contact-list .icon { position: absolute; left: 84px; top: 8px; width: 20px; height: 20px; }
  .contact-list li + li .icon { top: 10px; }
</style>
</head>
<body>
<div class="canvas">

  <!-- Front side -->
  <section class="page page--front">
    <svg class="layer" width="752" height="1068" viewBox="0 0 869 1200" preserveAspectRatio="none" role="img" aria-label="Photo of open hands holding raw amethyst crystals, with beaded bracelets and a teal scarf, in deep blue and purple tones">
      <defs>
        <linearGradient id="heroTone" x1="0" y1="0" x2="1" y2="1">
          <stop offset="0" stop-color="#2c2a7a"/>
          <stop offset="0.35" stop-color="#3f3fa0"/>
          <stop offset="0.6" stop-color="#8d86c8"/>
          <stop offset="0.8" stop-color="#5a4fb0"/>
          <stop offset="1" stop-color="#2b2782"/>
        </linearGradient>
        <radialGradient id="heroGlow" cx="0.55" cy="0.55" r="0.45">
          <stop offset="0" stop-color="#d9c9e6" stop-opacity="0.75"/>
          <stop offset="1" stop-color="#d9c9e6" stop-opacity="0"/>
        </radialGradient>
      </defs>
      <path d="M0 188 C 300 168, 600 150, 869 128 L869 810 C 760 820, 650 790, 560 730 C 420 640, 200 600, 0 650 Z" fill="url(#heroTone)"/>
      <path d="M0 188 C 300 168, 600 150, 869 128 L869 810 C 760 820, 650 790, 560 730 C 420 640, 200 600, 0 650 Z" fill="url(#heroGlow)"/>
    </svg>

    <svg class="layer" width="752" height="1068" viewBox="0 0 869 1200" preserveAspectRatio="none" aria-hidden="true">
      <path d="M0 0 H869 V128 C 600 150, 300 168, 0 188 Z" fill="var(--white)"/>
      <path d="M0 188 C 300 168, 600 150, 869 128 L869 142 C 600 165, 300 182, 0 198 Z" fill="var(--green)"/>
      <path d="M0 640 C 200 588, 430 600, 640 640 C 740 660, 810 650, 869 640 L869 660 C 800 672, 720 676, 630 660 C 420 622, 200 612, 0 660 Z" fill="var(--green)"/>
      <path d="M0 660 C 200 612, 420 622, 630 660 C 720 676, 800 672, 869 660 L869 810 C 760 820, 650 790, 560 730 C 420 640, 200 600, 0 650 Z" fill="var(--blue)"/>
      <path d="M0 668 C 200 615, 420 652, 560 740 C 650 798, 760 830, 869 820 V1200 H0 Z" fill="var(--white)"/>
      <path d="M0 1200 C 250 1176, 500 1172, 869 1180 V1200 Z" fill="var(--blue)"/>
      <path d="M300 1200 C 500 1184, 700 1184, 869 1190 V1200 Z" fill="var(--green)"/>
    </svg>

    <svg class="layer" style="left:510px;top:456px" width="240" height="240" viewBox="0 0 240 240" role="img" aria-label="Photo of a woman in white sitting cross-legged in meditation facing the ocean">
      <defs>
        <linearGradient id="seaTone" x1="0" y1="0" x2="0" y2="1">
          <stop offset="0" stop-color="#a9cde0"/>
          <stop offset="0.45" stop-color="#2f8fa8"/>
          <stop offset="0.7" stop-color="#6fb7c4"/>
          <stop offset="1" stop-color="#e7dccb"/>
        </linearGradient>
      </defs>
      <circle cx="120" cy="120" r="119" fill="var(--white)"/>
      <circle cx="120" cy="120" r="111" fill="var(--blue)"/>
      <circle cx="120" cy="120" r="105" fill="url(#seaTone)"/>
    </svg>

    <div class="brand-bar"></div>
    <div class="brand-mark"></div>
    <span class="brand-name">Dr. Elena Hartwell</span>

    <h1 class="hero-title">
      <span class="accent">Holistic Psychology</span><br>
      &amp; Sports Psychology<br>
      Consulting
    </h1>

    <div class="section-head">
      <p class="kicker">Ways to Improve</p>
      <p class="headline">Athletic Performance</p>
      <p class="sub">Using Sports and Holistic Psychology</p>
    </div>
    <div class="section-rule"></div>

    <ul class="services">
      <li>
        <svg class="tick" viewBox="0 0 20 20" aria-hidden="true"><circle cx="10" cy="10" r="9" fill="var(--green)" stroke="var(--navy)" stroke-width="1.5"/><path d="M5.5 10.5 L8.8 13.5 L14.5 6.8" fill="none" stroke="var(--navy)" stroke-width="2.2" stroke-linecap="round" stroke-linejoin="round"/></svg>
        <span class="label">Mental Skills Training –</span> Ex: visualization, goal-setting, motivation, self- talk, mindset, concentration techniques.
      </li>
      <li>
        <svg class="tick" viewBox="0 0 20 20" aria-hidden="true"><circle cx="10" cy="10" r="9" fill="var(--green)" stroke="var(--navy)" stroke-width="1.5"/><path d="M5.5 10.5 L8.8 13.5 L14.5 6.8" fill="none" stroke="var(--navy)" stroke-width="2.2" stroke-linecap="round" stroke-linejoin="round"/></svg>
        <span class="label">Performance Enhancement –</span> eliminate psychological barriers that are hindering performance such as self- doubt, perfectionism, fear of failure, and burnout.
      </li>
      <li>
        <svg class="tick" viewBox="0 0 20 20" aria-hidden="true"><circle cx="10" cy="10" r="9" fill="var(--green)" stroke="var(--navy)" stroke-width="1.5"/><path d="M5.5 10.5 L8.8 13.5 L14.5 6.8" fill="none" stroke="var(--navy)" stroke-width="2.2" stroke-linecap="round" stroke-linejoin="round"/></svg>
        <span class="label">Mental Health -</span> anxiety and stress management by using relaxation techniques, breathwork, and mindfulness practices.
      </li>
      <li>
        <svg class="tick" viewBox="0 0 20 20" aria-hidden="true"><circle cx="10" cy="10" r="9" fill="var(--green)" stroke="var(--navy)" stroke-width="1.5"/><path d="M5.5 10.5 L8.8 13.5 L14.5 6.8" fill="none" stroke="var(--navy)" stroke-width="2.2" stroke-linecap="round" stroke-linejoin="round"/></svg>
        <span class="label">Injury Recovery Support -</span> assist athletes in maintaining resilience and positive mental attitude during rehabilitation as well as processing emotions relating to any potential trauma caused by the injury or life transitions resulting from it.
      </li>
      <li>
        <svg class="tick" viewBox="0 0 20 20" aria-hidden="true"><circle cx="10" cy="10" r="9" fill="var(--green)" stroke="var(--navy)" stroke-width="1.5"/><path d="M5.5 10.5 L8.8 13.5 L14.5 6.8" fill="none" stroke="var(--navy)" stroke-width="2.2" stroke-linecap="round" stroke-linejoin="round"/></svg>
        <span class="label">Burnout prevention -</span> teach athletes how to have balance in sports and life so they can experience longevity in their sports as well as overall optimal health and well-being.
      </li>
    </ul>
  </section>

  <!-- Back side -->
  <section class="page page--back">
    <svg class="layer" width="752" height="1068" viewBox="0 0 752 1068" aria-hidden="true">
      <path d="M0 340 C 250 322, 500 308, 752 296 V720 H0 Z" fill="var(--navy)"/>
      <path d="M0 330 C 250 312, 500 298, 752 286 L752 302 C 500 314, 250 328, 0 346 Z" fill="var(--green)"/>
    </svg>

    <svg class="layer" style="top:344px" width="440" height="370" viewBox="0 0 440 370" role="img" aria-label="Illustration of a glowing figure meditating inside a head silhouette, in blue and violet light">
      <defs>
        <radialGradient id="auraTone" cx="0.45" cy="0.45" r="0.6">
          <stop offset="0" stop-color="#7b3fc0"/>
          <stop offset="0.35" stop-color="#5a6fd8"/>
          <stop offset="0.65" stop-color="#3d8ce0"/>
          <stop offset="1" stop-color="#27236b"/>
        </radialGradient>
      </defs>
      <rect width="440" height="370" fill="url(#auraTone)"/>
    </svg>

    <svg class="layer" width="752" height="1068" viewBox="0 0 752 1068" role="img" aria-label="Photo of a family walking on a beach at dusk">
      <defs>
        <linearGradient id="beachTone" x1="0" y1="0" x2="0.6" y2="1">
          <stop offset="0" stop-color="#5b6166"/>
          <stop offset="0.6" stop-color="#3a3d40"/>
          <stop offset="1" stop-color="#151617"/>
        </linearGradient>
      </defs>
      <path d="M0 712 C 250 698, 500 688, 752 700 V1068 H0 Z" fill="url(#beachTone)"/>
    </svg>

    <svg class="layer" width="752" height="1068" viewBox="0 0 752 1068" aria-hidden="true">
      <path d="M380 706 C 520 684, 650 680, 752 690 V716 C 650 706, 520 708, 380 722 Z" fill="var(--green)"/>
      <path d="M0 1068 C 250 1050, 500 1048, 752 1056 V1068 Z" fill="var(--blue)"/>
      <path d="M260 1068 C 450 1058, 620 1058, 752 1062 V1068 Z" fill="var(--green)"/>
    </svg>

    <svg class="layer" style="left:425px;top:656px" width="280" height="280" viewBox="0 0 280 280" role="img" aria-label="Portrait photo of the psychologist with her golden retriever">
      <defs>
        <linearGradient id="portraitTone" x1="0" y1="0" x2="0" y2="1">
          <stop offset="0" stop-color="#9fb7c9"/>
          <stop offset="0.5" stop-color="#6e5a52"/>
          <stop offset="1" stop-color="#d9c29a"/>
        </linearGradient>
      </defs>
      <circle cx="140" cy="140" r="139" fill="var(--white)"/>
      <circle cx="140" cy="140" r="130" fill="var(--blue)"/>
      <circle cx="140" cy="140" r="122" fill="url(#portraitTone)"/>
    </svg>

    <h2 class="about-tab">ABOUT ME</h2>
    <p class="about-text"><strong>Dr. Elena Hartwell</strong> is a licensed psychologist. She understands the unique experiences of athletes due to her background as an All-American swimmer, collegiate and age group swim coach, parent of a collegiate/professional athlete, and sports psychology researcher. She works with athletes to optimize performance and overall well-being.</p>
    <p class="about-text"><span class="lead">Her specializations include:</span> performance anxiety, mental performance, stress management, anxiety, depressions, trauma, life transitions, relationship issues, injury, and sleep.</p>

    <p class="telehealth">All services are<br>provided online<br><span class="accent">via telehealth</span></p>
    <p class="sessions">Sessions are</p>
    <p class="sessions-pill">30 or 55 min</p>

    <p class="contact-tab">Contact info:</p>
    <ul class="contact-list">
      <li>
        <svg class="icon" viewBox="0 0 20 20" aria-hidden="true"><path d="M10 1.5 C6.4 1.5 4 4 4 7.3 C4 11.5 10 18.5 10 18.5 C10 18.5 16 11.5 16 7.3 C16 4 13.6 1.5 10 1.5 Z" fill="var(--green)"/><circle cx="10" cy="7.3" r="2.3" fill="#4a4e52"/></svg>
        2280 Harbor View Lane #105<br>Coral Bay, FL 32099
      </li>
      <li>
        <svg class="icon" viewBox="0 0 20 20" aria-hidden="true"><path d="M5 2 L8 2 L9.5 6 L7.5 7.5 C8.5 9.8 10.2 11.5 12.5 12.5 L14 10.5 L18 12 L18 15 C18 16.5 16.8 17.5 15.3 17.3 C8.5 16.5 3.5 11.5 2.7 4.7 C2.5 3.2 3.5 2 5 2 Z" fill="none" stroke="var(--green)" stroke-width="1.8" stroke-linejoin="round"/></svg>
        904-555-0187
      </li>
      <li>
        <svg class="icon" viewBox="0 0 20 20" aria-hidden="true"><g fill="none" stroke="var(--green)" stroke-width="1.6"><circle cx="10" cy="10" r="8"/><ellipse cx="10" cy="10" rx="3.6" ry="8"/><path d="M2 10 H18 M3.3 5.5 H16.7 M3.3 14.5 H16.7"/></g></svg>
        www.drelenahartwell.com
      </li>
    </ul>
  </section>

</div>
</body>
</html>
```